Bramblewood Card Company Business Cards

We are a trading card store with Glimmorax, sports and other TCG cards, we need a business card design that encompasses a clean cut, modern style with a retro flare. website is bramblewoodcardco.com for reference. Can utilize a comic book era feel or a more modern outdoor feel to utilize the "Pacific Northwest" elements of tress, mountains, etc.

Industry/Entity Type

Trading cards and collectibles

Contact Information for Business Card

business name, email address, phone number, name, owner job title

Font styles to use
Sans Serif

```html
<!DOCTYPE html>
<html lang="en">
<head>
<meta charset="utf-8">
<title>Bramblewood Card Company – Business Cards</title>
<link href="https://fonts.googleapis.com/css2?family=Montserrat:wght@400;500;700;800&display=swap" rel="stylesheet">
<style>
  :root {
    --backdrop: #d3d6d7;
    --paper: #f7f7f5;
    --teal: #1b9cc4;
    --charcoal: #3d3f41;
    --ink: #2a2a2a;
    --rule: #8a8a8a;
    --slash: #c9d3d6;
  }
  * { margin: 0; padding: 0; box-sizing: border-box; }
  html, body { width: 1200px; height: 829px; overflow: hidden; }
  body {
    background: var(--backdrop);
    font-family: "Montserrat", sans-serif;
    position: relative;
  }
  .card {
    position: absolute;
    width: 500px;
    height: 286px;
    background: var(--paper);
    border-bottom: 4px solid var(--teal);
    box-shadow: 0 10px 24px rgba(0,0,0,0.12);
    overflow: hidden;
  }
  .card--front { left: 70px; top: 272px; }
  .card--back { left: 630px; top: 272px; }

  .holder { position: absolute; left: 34px; top: 38px; }
  .holder__name {
    color: var(--teal);
    font-weight: 800;
    font-size: 22px;
    letter-spacing: 1px;
    text-transform: uppercase;
    line-height: 1.1;
  }
  .holder__title { color: var(--ink); font-size: 12px; margin-top: 3px; }
  .holder__rule { width: 70px; height: 1px; background: var(--rule); margin: 10px 0 12px; }

  .contact-list { list-style: none; }
  .contact-list li {
    display: flex; align-items: center; gap: 8px;
    font-size: 11.5px; color: var(--ink); margin-bottom: 6px;
    white-space: nowrap;
  }
  .contact-list svg { width: 10px; height: 10px; fill: var(--teal); flex: none; }

  .divider {
    position: absolute; left: 34px; right: 34px; top: 176px;
    height: 1px; background: var(--rule);
  }

  .brand-mark {
    position: absolute;
    display: flex; align-items: center; gap: 10px;
    color: var(--charcoal);
    font-weight: 700;
    text-transform: uppercase;
    letter-spacing: 1px;
    line-height: 1.3;
    white-space: nowrap;
  }
  .brand-mark__name span { display: block; }
  .brand-mark__dot { border-radius: 50%; background: var(--teal); flex: none; }
  .card--front .brand-mark { right: 30px; top: 62px; font-size: 12px; }
  .card--front .brand-mark__dot { width: 18px; height: 18px; }
  .card--back .brand-mark {
    left: 50%; top: 50%; transform: translate(-50%, -50%);
    font-size: 19px;
  }
  .card--back .brand-mark__dot { width: 30px; height: 30px; }

  .address {
    position: absolute; right: 34px; top: 192px;
    text-align: right; font-size: 12px; font-style: normal;
    color: var(--ink); line-height: 1.45; white-space: nowrap;
  }
  .footer-band { position: absolute; left: 0; bottom: 0; width: 500px; height: 18px; }
</style>
</head>
<body>
  <section class="card card--front" aria-label="Business card front">
    <div class="holder">
      <h1 class="holder__name">Dorian Hale</h1>
      <p class="holder__title">CEO/Founder</p>
      <div class="holder__rule"></div>
      <ul class="contact-list">
        <li><svg viewBox="0 0 10 10" aria-hidden="true"><path d="M2 0.5 L3.6 2.6 L2.8 3.6 Q3.8 5.8 6.3 7.1 L7.3 6.3 L9.5 7.9 L8.4 9.6 Q3.8 9 0.5 1.6 Z"/></svg>(555) 274 6190</li>
        <li><svg viewBox="0 0 10 10" aria-hidden="true"><path d="M0 2 H10 V8.5 H0 Z M0.6 2.4 L5 5.6 L9.4 2.4" stroke="#f7f7f5" stroke-width="0.8"/></svg>info@bramblewoodcardco.com</li>
        <li><svg viewBox="0 0 10 10" aria-hidden="true"><circle cx="5" cy="5" r="4.6"/><path d="M0.4 5 H9.6 M5 0.4 V9.6 M1.5 2.6 H8.5 M1.5 7.4 H8.5" stroke="#f7f7f5" stroke-width="0.6" fill="none"/></svg>www.bramblewoodcardco.com</li>
      </ul>
    </div>

    <div class="brand-mark">
      <span class="brand-mark__dot"></span>
      <span class="brand-mark__name"><span>Bramblewood</span><span>Card Company</span></span>
    </div>

    <div class="divider"></div>

    <address class="address">
      P.O. Box 3817 Alder Lane<br>Cedar Ridge WA 98214
    </address>

    <svg class="footer-band" viewBox="0 0 500 18" preserveAspectRatio="none" aria-hidden="true">
      <polygon points="0,0 190,0 182,18 0,18" fill="var(--teal)"/>
      <polygon points="194,0 200,0 192,18 186,18" fill="var(--slash)"/>
      <polygon points="204,0 500,0 500,18 196,18" fill="var(--charcoal)"/>
    </svg>
  </section>

  <section class="card card--back" aria-label="Business card back">
    <div class="brand-mark">
      <span class="brand-mark__dot"></span>
      <span class="brand-mark__name"><span>Bramblewood</span><span>Card Company</span></span>
    </div>
  </section>
</body>
</html>
```